Velmora Freightway Solutions Business cards

Would like a very unique design catchy but professional for business cards. Please use log provided.Marlon WellsCeo and Founder TransCon Logistix Solutions1-888-913-3225mwells@tlsolutionsus.comwww.tlsolutionsus.com

```html
<!DOCTYPE html>
<html lang="en">
<head>
<meta charset="utf-8">
<title>Velmora Freightway Solutions – Business Cards</title>
<link href="https://fonts.googleapis.com/css2?family=Lato:wght@400;700&display=swap" rel="stylesheet">
<style>
  :root {
    --backdrop: #4e3f36;
    --brand-blue: #1273c1;
    --brand-red: #e3232c;
    --navy: #0f2a45;
    --ink: #1d1d1d;
    --paper: #ffffff;
  }
  * { margin: 0; padding: 0; box-sizing: border-box; }
  html, body { width: 1200px; height: 960px; overflow: hidden; }
  body {
    background: var(--backdrop);
    font-family: "Lato", Arial, sans-serif;
    position: relative;
  }
  .card {
    position: absolute;
    border-radius: 34px;
    overflow: hidden;
    box-shadow: 0 6px 14px rgba(0,0,0,0.35);
  }
  /* Front */
  .card-front {
    left: 236px; top: 47px; width: 722px; height: 406px;
    background: var(--brand-blue);
    color: var(--paper);
    text-align: center;
  }
  .front-name {
    position: absolute; left: 0; right: 0; top: 128px;
    font-size: 54px; font-weight: 700; line-height: 1.15;
    letter-spacing: 1px;
  }
  .front-url {
    position: absolute; left: 0; right: 0; top: 300px;
    font-size: 19px; font-weight: 700; letter-spacing: 3px;
  }
  /* Back */
  .card-back {
    left: 245px; top: 507px; width: 703px; height: 408px;
    background: var(--paper);
  }
  .name-marker {
    position: absolute; left: 0; top: 55px; width: 10px; height: 55px;
    background: var(--brand-blue);
  }
  .person-name {
    position: absolute; left: 31px; top: 52px;
    font-size: 24px; font-weight: 700; color: var(--brand-blue);
  }
  .person-title {
    position: absolute; left: 31px; top: 86px;
    font-size: 19px; font-weight: 400; color: var(--brand-red);
  }
  .company-name {
    position: absolute; left: 340px; top: 50px; width: 340px;
    font-size: 27px; font-weight: 700; line-height: 1.2;
    color: var(--brand-blue); text-align: center;
  }
  .contact-list {
    position: absolute; left: 30px; top: 242px; list-style: none;
  }
  .contact-list li {
    display: flex; align-items: center; gap: 10px;
    font-size: 17px; color: var(--ink); height: 30px;
  }
  .contact-list svg { width: 16px; height: 16px; flex: none; }
  .footer-band { position: absolute; left: 0; bottom: 0; width: 703px; height: 56px; }
  .address {
    position: absolute; left: 32px; top: 355px;
    font-size: 17px; color: var(--paper);
  }
</style>
</head>
<body>
  <section class="card card-front">
    <div class="front-name">Velmora Freightway<br>Solutions</div>
    <div class="front-url">www.vfwayroutes.com</div>
  </section>

  <section class="card card-back">
    <div class="name-marker"></div>
    <div class="person-name">DORIAN PIKE</div>
    <div class="person-title">CEO AND FOUNDER</div>

    <div class="company-name">Velmora Freightway Solutions</div>

    <ul class="contact-list">
      <li>
        <svg viewBox="0 0 16 16" aria-hidden="true"><circle cx="8" cy="8" r="7" fill="none" stroke="#1273c1" stroke-width="1.4"/><path d="M5.5 4.5l1.5 1.6-.9 1.1c.6 1.2 1.4 2 2.6 2.6l1.1-.9 1.6 1.5-1 1.2C7.6 11.4 4.6 8.4 4.4 5.5z" fill="#1273c1"/></svg>
        <span>1-888-470-6158</span>
      </li>
      <li>
        <svg viewBox="0 0 16 16" aria-hidden="true"><rect x="1" y="3.5" width="14" height="10" rx="1.5" fill="#1273c1"/><path d="M1.5 4.5L8 9.5l6.5-5" fill="none" stroke="#fff" stroke-width="1.3"/></svg>
        <span>dpike@vfwayroutes.com</span>
      </li>
      <li>
        <svg viewBox="0 0 16 16" aria-hidden="true"><g fill="none" stroke="#1273c1" stroke-width="1.2"><circle cx="8" cy="8" r="6.5"/><ellipse cx="8" cy="8" rx="3" ry="6.5"/><path d="M1.5 8h13M2.5 4.8h11M2.5 11.2h11"/></g></svg>
        <span>www.vfwayroutes.com</span>
      </li>
    </ul>

    <svg class="footer-band" viewBox="0 0 703 56" preserveAspectRatio="none" aria-hidden="true">
      <path d="M0 2 H703 V56 H0 Z" fill="#1273c1"/>
      <path d="M0 0 H470 C452 0 455 30 430 30 H0 Z" fill="#0f2a45"/>
    </svg>
    <div class="address">2145 Larkspur Ridge Rd, Atlanta, GA 30322</div>
  </section>
</body>
</html>
```